Verodex business card

Business card for sustainable investment company called "Verodex". Verodex is an exchange platform selling carbon credits between buyers and sellers. Carbon Credits are an environmental commodity for reducing global carbon emissions.

the card should obviously have our logo and the theme should be sustainability/environment mixed with a trading platform.

Contact Information for Business Card

Logo, Name, Title, Phone, Email

Colors
0054AA
0677BA
7BADD7
CADEEF
E8F1F8
0094D4
00A9DD
6FCCEA
C7EBF8
E9F6FB
00AB8E
00BBA5
67D7C9
C6EFE9
E9F9F6
59FF00
82FF00
B8FF75
E3FFCB
F4FFEA

```html
<!DOCTYPE html>
<html lang="en">
<head>
<meta charset="utf-8">
<title>Verodex business card</title>
<link rel="stylesheet" href="https://fonts.googleapis.com/css2?family=Montserrat:wght@700&family=Open+Sans:wght@400;700&display=swap">
<style>
  :root {
    --backdrop: #e7e9ec;
    --card: #1f2024;
    --card-edge: #2a2b30;
    --ink-light: #ffffff;
    --ink-muted: #e4e6ea;
    --accent: #4a9fd8;
    --accent-deep: #0677ba;
    --accent-soft: #6fccea;
    --emboss: #2b2c31;
    --emboss-dark: #17181b;
  }
  * { box-sizing: border-box; margin: 0; padding: 0; }
  html, body { width: 1200px; height: 780px; overflow: hidden; }
  body {
    background: var(--backdrop);
    display: flex;
    align-items: center;
    justify-content: center;
    gap: 40px;
    font-family: "Open Sans", Arial, sans-serif;
  }
  .card {
    position: relative;
    width: 540px;
    height: 320px;
    background: var(--card);
    border-radius: 22px;
    box-shadow: 0 3px 0 var(--card-edge), 0 14px 30px rgba(0,0,0,.25);
    overflow: hidden;
  }
  /* front */
  .brand {
    position: absolute;
    top: 30px;
    left: 34px;
    display: flex;
    align-items: center;
    gap: 12px;
  }
  .brand-square {
    width: 22px;
    height: 22px;
    background: var(--accent);
  }
  .brand-name {
    font-family: "Montserrat", Arial, sans-serif;
    font-weight: 700;
    font-size: 30px;
    letter-spacing: 1px;
    color: var(--ink-light);
    text-transform: uppercase;
  }
  .person {
    position: absolute;
    top: 38px;
    right: 40px;
    text-align: right;
  }
  .person-name {
    font-weight: 700;
    font-size: 27px;
    color: var(--accent);
    letter-spacing: .3px;
  }
  .person-title {
    font-size: 15px;
    color: var(--ink-light);
    letter-spacing: .5px;
    margin-top: 2px;
  }
  .edge-tab {
    position: absolute;
    top: 40px;
    right: 0;
    width: 14px;
    height: 58px;
    background: linear-gradient(180deg, var(--accent-soft), var(--accent-deep));
  }
  .contact {
    position: absolute;
    left: 34px;
    bottom: 34px;
    list-style: none;
    color: var(--ink-muted);
    font-size: 13px;
    line-height: 1.55;
  }
  .contact-address { margin-bottom: 8px; }
  .contact-line { display: flex; align-items: center; gap: 8px; }
  .contact-line svg { width: 13px; height: 13px; flex: none; }
  .watermark {
    position: absolute;
    right: 30px;
    bottom: 22px;
    font-family: "Montserrat", Arial, sans-serif;
    font-weight: 700;
    font-size: 64px;
    color: var(--emboss);
    text-transform: uppercase;
    letter-spacing: 2px;
    text-shadow: 0 2px 0 var(--emboss-dark);
  }
  /* back */
  .card-back {
    display: flex;
    align-items: center;
    justify-content: center;
    gap: 14px;
  }
  .back-square {
    width: 34px;
    height: 34px;
    background: var(--emboss);
    box-shadow: 0 2px 0 var(--emboss-dark);
  }
  .back-name {
    font-family: "Montserrat", Arial, sans-serif;
    font-weight: 700;
    font-size: 46px;
    letter-spacing: 1.5px;
    color: var(--emboss);
    text-transform: uppercase;
    text-shadow: 0 2px 0 var(--emboss-dark);
  }
</style>
</head>
<body>

<section class="card card-front">
  <div class="brand">
    <span class="brand-square"></span>
    <span class="brand-name">Verodex</span>
  </div>

  <div class="person">
    <p class="person-name">Marta Kolinova</p>
    <p class="person-title">Managing Director</p>
  </div>
  <span class="edge-tab"></span>

  <ul class="contact">
    <li class="contact-address">480 Linden Ave. Suite 12<br>Dayton, OH 45402</li>
    <li class="contact-line">
      <svg viewBox="0 0 16 16" aria-hidden="true"><circle cx="8" cy="8" r="8" fill="#4a9fd8"/><path d="M5.2 4.2l1.6-.4.9 2-1 .8a5 5 0 0 0 2.7 2.7l.8-1 2 .9-.4 1.6c-3.6.2-6.8-3-6.6-6.6z" fill="#1f2024"/></svg>
      (555) 214-0386
    </li>
    <li class="contact-line">
      <svg viewBox="0 0 16 16" aria-hidden="true"><circle cx="8" cy="8" r="8" fill="#4a9fd8"/><rect x="4" y="5" width="8" height="6" fill="#1f2024"/><path d="M4 5l4 3.3L12 5" stroke="#4a9fd8" stroke-width="1" fill="none"/></svg>
      info@verodex.com
    </li>
    <li class="contact-line">
      <svg viewBox="0 0 16 16" aria-hidden="true"><circle cx="8" cy="8" r="8" fill="#4a9fd8"/><circle cx="8" cy="8" r="4.5" fill="none" stroke="#1f2024" stroke-width="1.1"/><path d="M3.5 8h9M8 3.5c-2 2.5-2 6.5 0 9M8 3.5c2 2.5 2 6.5 0 9" fill="none" stroke="#1f2024" stroke-width="1"/></svg>
      www.verodex.com
    </li>
  </ul>

  <span class="watermark">Verodex</span>
</section>

<section class="card card-back">
  <span class="back-square"></span>
  <span class="back-name">Verodex</span>
</section>

</body>
</html>
```